Business Card for a Jewellery Brand

Business card for an upscale jewellery brand. Attached is the brand logo and icon and color board. I am looking for two card versions: one for the founder and one is generic. The card should be elegant and convey upscale and premium feel. I am open to both square and rectangle card shapes.

Industry/Entity Type

Jewelry

Contact Information for Business Card

Two cards: (1) Sunela Parvaniya (Founder) (2) General
(1) Sunela Parvaniya card should have Name: Sunela Parvaniya, Title: Founder Email id: sunela@quiremo.com.au. Phone no: +61452913307
(2) Generic card should have Email id: info@quiremo.com.au. Phone no: +61436207518

Requirements
Must have
• Workmark
• ICON
• Phone no
• Email ID
• ABN: 58219740312 (Note: ABN is Business number in Australia)
• Website: www.quiremo.com.au
• Instagram: quiremo_jewellery
• Facebook: @quiremojewellery
Nice to have
• Tagline

```html
<!DOCTYPE html>
<html lang="en">
<head>
<meta charset="utf-8">
<title>Quiremo Business Cards</title>
<link rel="stylesheet" href="https://fonts.googleapis.com/css2?family=Lato:wght@300;400;700&display=swap">
<style>
  :root {
    --backdrop: #e6e6e1;
    --card-rose: #e0918c;
    --card-charcoal: #2a2a2b;
    --foil-rose: #9a6d66;
    --foil-silver: #d9d9d9;
    --ink-light: #c9c9c9;
    --ink-muted: #9d9d9d;
  }
  * { box-sizing: border-box; margin: 0; padding: 0; }
  html, body {
    width: 1200px; height: 1200px; overflow: hidden;
    background: var(--backdrop);
    font-family: "Lato", sans-serif;
  }
  .sheet {
    width: 1200px; height: 1200px;
    display: flex; flex-direction: column; align-items: center; justify-content: center;
    gap: 64px;
  }
  .card {
    position: relative;
    width: 760px; height: 463px;
    box-shadow: 0 14px 30px rgba(0,0,0,0.12);
  }
  /* Front */
  .card--front {
    background: var(--card-rose);
    display: flex; flex-direction: column; align-items: center; justify-content: center;
  }
  .front-wordmark {
    font-weight: 300;
    font-size: 72px;
    letter-spacing: 0.32em;
    margin-right: -0.32em;
    color: var(--foil-rose);
  }
  .front-tagline {
    margin-top: 14px;
    font-weight: 400;
    font-size: 19px;
    letter-spacing: 0.04em;
    color: var(--foil-rose);
  }
  /* Back */
  .card--back {
    background: var(--card-charcoal);
    color: var(--ink-light);
  }
  .back-wordmark {
    position: absolute; top: 52px; right: 58px;
    font-weight: 300;
    font-size: 58px;
    letter-spacing: 0.3em;
    margin-right: -0.3em;
    color: var(--foil-silver);
  }
  .back-website {
    position: absolute; top: 222px; right: 58px;
    font-size: 18px; font-weight: 400; color: var(--ink-muted);
  }
  .identity {
    position: absolute; top: 205px; left: 44px;
    padding-left: 24px;
    border-left: 9px solid var(--foil-silver);
  }
  .identity-name {
    font-size: 24px; font-weight: 400; color: var(--foil-silver); line-height: 1.1;
  }
  .identity-name strong { font-weight: 700; }
  .identity-title {
    font-size: 17px; color: var(--ink-muted); margin-top: 4px;
  }
  .contact-list {
    position: absolute; top: 300px; left: 77px;
    list-style: none;
    font-size: 18px; color: var(--ink-light);
  }
  .contact-list li {
    display: flex; align-items: center; gap: 10px;
    height: 28px;
  }
  .contact-list .abn { margin-bottom: 6px; }
  .contact-icon { width: 16px; height: 16px; flex: none; }
  .contact-dot {
    width: 14px; height: 14px; flex: none;
    background: var(--ink-light); border-radius: 2px;
  }
</style>
</head>
<body>
<main class="sheet">
  <section class="card card--front" aria-label="Card front">
    <div class="front-wordmark">QUIREMO</div>
    <div class="front-tagline">EXQUISITE SILVER JEWELLERY</div>
  </section>

  <section class="card card--back" aria-label="Card back">
    <div class="back-wordmark">QUIREMO</div>
    <div class="back-website">www.quiremo.com.au</div>

    <div class="identity">
      <p class="identity-name">Sunela <strong>Parvaniya</strong></p>
      <p class="identity-title">Founder</p>
    </div>

    <ul class="contact-list">
      <li class="abn">ABN: 58219740312</li>
      <li>
        <svg class="contact-icon" viewBox="0 0 16 16" aria-hidden="true">
          <rect x="1" y="3" width="14" height="10" fill="#c9c9c9"/>
          <path d="M1 3 L8 9 L15 3" fill="none" stroke="#2a2a2b" stroke-width="1.4"/>
        </svg>
        sunela@quiremo.com.au
      </li>
      <li>
        <svg class="contact-icon" viewBox="0 0 16 16" aria-hidden="true">
          <path d="M1 5 Q8 0 15 5 L13 7 L11 5.5 L5 5.5 L3 7 Z" fill="#c9c9c9"/>
          <rect x="3" y="8" width="10" height="6" rx="1" fill="#c9c9c9"/>
        </svg>
        +61452913307
      </li>
      <li><span class="contact-dot"></span>quiremo_jewellery</li>
      <li><span class="contact-dot"></span>@quiremojewellery</li>
    </ul>
  </section>
</main>
</body>
</html>
```